Hardcore nerd needs to stand out in a sea of dull Defence business cards

Wombarra Devices is a new Australian consulting engineering company that turns research and theory into practical systems. No evangelistic fluff, just mathematics and physics into electronic and optical circuits for consumer products, scientific research or Defence applications.

We already have a recognised logo (provided) which is often dark blue/black on a light background but we're open to other combinations. (Us engineers tend to have limited aesthetic imagination :)

Some of our recent products have included:
* Instrumentation for electrical testing,
* Radar jammers,
* GPS antenna design,
* Satellite tracking systems,
* High power lasers

We're open to both single and double-sided designs - happy to be convinced either way.

P.S. Another group is working on the web page, so - alas - our web site is currently of no use for images/ideas...

Target Market(s)

Engineering managers,
Scientists

Contact Information for Business Card

Dr Colin Harte
R&D Engineer

colin@wombarradevices.com.au
0427 563 710

PO Box XXX (to be confirmed)
Kelsby ACT 2917
Australia

Font styles to use
Serif
Sans Serif

Colors

Designer to choose colors to be used in the design.

Requirements
Must have
• My contact details!
• I've had many (great) "bold and plain" designs submitted already, so feel free to be artistically creative :)
• Happy to take advice re fonts/colours/printability etc.
Nice to have
• I'm not sure if "lists" are more at home on a CV than a business card, but representative services include:
• Applied electromagnetics
• RF and high speed electronics
• Signal and image processing
• Electro-optical and laser systems
• Concept-to-prototype design services
• If you're considering double sided cards, then often measuring/alignment grids/rulers feature on the back of similar cards.
• e.g. https://www.veltranoptics.example/newgrouppage9.cfm?objectgroup_id=4183
• https://www.veltranoptics.example/newgrouppage9.cfm?objectgroup_ID=4185
• ..or even a "Smith chart" (google will return lots)
• Generic images to represent a capability might work - googling images associated with keyword for each of these areas might help:
• - "passive radar", "phased array", "fdtd", "vircator"
• RF and high speed electronic design
• - "smith chart", "microstrip circuits", "dimensioned drawing", "electronic schematic"
• - "dft", "iir filter"
• - "optical cavity". "laser energy level diagram"
• Background/watermarked images outlines/wireframes/schematics would probably look OK.
Should not have
• If a list of projects/services is provided, it is important not to make the client feel that this is "all" the company can do. Engineering design is a creative discipline (like graphics :)
• Please, no stock "military" snaps like planes, missiles, etc!

```html
<!DOCTYPE html>
<html lang="en">
<head>
<meta charset="utf-8">
<title>Wombarra Devices – Business Card</title>
<link rel="stylesheet" href="https://fonts.googleapis.com/css2?family=Lato:ital,wght@0,400;0,700;0,900;1,400;1,700&display=swap">
<style>
  :root {
    --navy: #1f2a5e;
    --orange: #f47f20;
    --white: #ffffff;
    --backdrop: #e9e6e1;
    --card-w: 620px;
    --card-h: 354px;
  }
  * { margin: 0; padding: 0; box-sizing: border-box; }
  html, body { width: 1200px; height: 989px; overflow: hidden; }
  body {
    background: var(--backdrop);
    font-family: "Lato", Arial, sans-serif;
    position: relative;
  }
  .card {
    position: absolute;
    width: var(--card-w);
    height: var(--card-h);
    overflow: hidden;
    box-shadow: 0 6px 18px rgba(0,0,0,0.18);
  }
  .card--back { left: 520px; top: 80px; background: var(--navy); }
  .card--front { left: 60px; top: 540px; background: var(--white); }

  .brand {
    position: absolute;
    left: 30px; top: 30px;
    display: flex; align-items: center; gap: 12px;
    z-index: 2;
  }
  .brand__dot {
    width: 34px; height: 34px; border-radius: 50%;
    background: var(--white);
  }
  .brand__name {
    color: var(--orange);
    font-weight: 900;
    font-size: 26px;
    letter-spacing: 1px;
    text-transform: uppercase;
  }

  /* Back */
  .back__band {
    position: absolute; left: 0; right: 0;
    top: 108px; height: 190px;
    background: var(--white);
  }
  .services {
    position: absolute; left: 0; right: 0; top: 130px;
    list-style: none; text-align: center;
    color: var(--navy); font-weight: 700; font-size: 21px; line-height: 29px;
  }

  /* Front */
  .front__panel { position: absolute; inset: 0; z-index: 1; }
  .front__name-band {
    position: absolute; left: 0; right: 0;
    top: 168px; height: 68px;
    background: var(--orange);
  }
  .person {
    position: absolute; right: 26px; top: 172px; text-align: right; z-index: 2;
  }
  .person__name { color: var(--navy); font-weight: 700; font-size: 30px; line-height: 34px; }
  .person__role { color: var(--white); font-style: italic; font-size: 19px; line-height: 24px; }
  .address {
    position: absolute; right: 26px; top: 262px; text-align: right;
    color: var(--navy); font-size: 21px; line-height: 26px; font-style: normal;
  }
  .contact {
    position: absolute; left: 30px; top: 150px; z-index: 2;
    color: var(--white); font-size: 17px; line-height: 26px;
  }
  .contact__row { display: flex; align-items: center; gap: 8px; }
  .contact__icon { width: 14px; height: 14px; flex: none; }
</style>
</head>
<body>

<section class="card card--back" aria-label="Card back">
  <div class="brand">
    <span class="brand__dot"></span>
    <span class="brand__name">Wombarra Devices</span>
  </div>
  <div class="back__band"></div>
  <ul class="services">
    <li>Radar jammers,</li>
    <li>High power lasers,</li>
    <li>GPS antenna design,</li>
    <li>Satellite tracking systems,</li>
    <li>Instrumentation for electrical testing</li>
  </ul>
</section>

<section class="card card--front" aria-label="Card front">
  <div class="front__name-band"></div>
  <svg class="front__panel" width="620" height="354" viewBox="0 0 620 354">
    <polygon points="0,0 330,0 360,354 0,354" fill="var(--navy)"/>
  </svg>
  <div class="brand">
    <span class="brand__dot"></span>
    <span class="brand__name">Wombarra Devices</span>
  </div>
  <div class="contact">
    <div class="contact__row">
      <svg class="contact__icon" viewBox="0 0 24 24"><path fill="#fff" d="M6.6 10.8a15.1 15.1 0 0 0 6.6 6.6l2.2-2.2a1 1 0 0 1 1-.25 11.4 11.4 0 0 0 3.6.57 1 1 0 0 1 1 1V20a1 1 0 0 1-1 1A17 17 0 0 1 3 4a1 1 0 0 1 1-1h3.5a1 1 0 0 1 1 1c0 1.25.2 2.45.57 3.57a1 1 0 0 1-.25 1z"/></svg>
      <span>0427 563 710</span>
    </div>
    <div class="contact__row">
      <svg class="contact__icon" viewBox="0 0 24 24"><rect x="2" y="5" width="20" height="14" fill="none" stroke="#fff" stroke-width="2"/><path d="M2 6l10 7 10-7" fill="none" stroke="#fff" stroke-width="2"/></svg>
      <span>colin@wombarradevices.com.au</span>
    </div>
  </div>
  <div class="person">
    <div class="person__name">Dr Colin Harte</div>
    <div class="person__role">R&amp;D Engineer</div>
  </div>
  <address class="address">
    PO Box XXX<br>
    Kelsby ACT 2917<br>
    Australia
  </address>
</section>

</body>
</html>
```